Norrell Advisory WA Business Card

Create an interesting, eye catching and colourful two sided business card. We are a business consulting operation assisting SME's improve all areas of their business. We provide consulting services to assist SME's to create a culture of continuous improvement, making a positive difference in the business. Our tag line is Small changes, big rewards. We want to create a well recognised, innovative brand that can be continued throughout our website, social media and email correspondence.

Target Market(s)

Small to Medium Enterprise Business Owners

Industry/Entity Type

Business Consultant

Contact Information for Business Card

Name of Business: Norrell Advisory - Steady Steps Strong Results
Derek Holloway Ph 0407385510 Megan Holloway Ph 0407913847
Email norrelladvisorywa@mailbox-example.com
Web address TBA
FaceBook page TBA

BACKSIDE OF CARD

Providing assistance with:

• Organisation & Efficiency
• Revenue generation & Marketing
• Financial Management
• Production quality & delivery
• Systems & Process documentation
• Exit Strategy

Font styles to use
Other font styles liked:
• Calibri

Colors

Designer to choose colors to be used in the design.

Requirements
Must have
• Calibri font

```html
<!DOCTYPE html>
<html lang="en">
<head>
<meta charset="utf-8">
<title>Norrell Advisory WA Business Card</title>
<link href="https://fonts.googleapis.com/css2?family=Carlito:ital,wght@0,400;0,700;1,400;1,700&display=swap" rel="stylesheet">
<style>
  :root {
    --backdrop: #e4e4e4;
    --card-dark: #262626;
    --card-dark-deep: #1c1c1c;
    --card-light: #ffffff;
    --ink-dark: #2b2b2b;
    --ink-muted: #555555;
    --ink-light: #c9c9c9;
    --ink-soft: #dcdcdc;
    --blue: #1a86c8;
    --red: #e8402f;
    --green: #6cb636;
    --orange: #f5a623;
  }
  * { box-sizing: border-box; margin: 0; padding: 0; }
  html, body {
    width: 1125px; height: 1200px; overflow: hidden;
    background: var(--backdrop);
    font-family: "Carlito", "Calibri", sans-serif;
  }
  .canvas { position: relative; width: 1125px; height: 1200px; }

  .card {
    position: absolute; left: 171px; width: 826px; height: 472px;
    border-radius: 24px; overflow: hidden;
    background: linear-gradient(160deg, var(--card-dark) 0%, var(--card-dark-deep) 100%);
  }
  .card--front { top: 106px; }
  .card--back { top: 639px; }

  /* front: brand panel */
  .brand-panel {
    position: absolute; left: 0; top: 0; width: 407px; height: 100%;
    background: var(--card-light);
    display: flex; flex-direction: column; align-items: center;
    padding-top: 150px;
  }
  .brand-panel__mark {
    width: 72px; height: 72px; background: var(--blue); margin-bottom: 42px;
  }
  .brand-panel__name {
    font-weight: 700; font-size: 32px; line-height: 1; color: var(--ink-dark); letter-spacing: 0.2px;
  }
  .brand-panel__tagline {
    font-size: 13.5px; color: var(--ink-muted); letter-spacing: 4px; margin-top: 4px;
  }

  .colour-stripe {
    position: absolute; left: 409px; top: 0; width: 8px; height: 100%;
    display: flex; flex-direction: column;
  }
  .colour-stripe span { flex: 1; }
  .colour-stripe .blue { background: var(--blue); }
  .colour-stripe .red { background: var(--red); }
  .colour-stripe .green { background: var(--green); }
  .colour-stripe .orange { background: var(--orange); }

  .contact-panel { position: absolute; left: 470px; top: 112px; color: var(--ink-light); }
  .person { margin-bottom: 14px; }
  .person__name { font-weight: 700; font-size: 33px; line-height: 1; }
  .person__phone { font-weight: 700; font-size: 27px; line-height: 1.1; letter-spacing: 0.5px; }
  .contact-list { list-style: none; margin-top: 24px; }
  .contact-list li {
    display: flex; align-items: center; gap: 9px;
    font-size: 17.5px; line-height: 25px; color: var(--ink-light);
  }
  .contact-list svg { width: 17px; height: 17px; flex: none; }

  /* back */
  .back-brand {
    position: absolute; left: 95px; top: 0; width: 250px; height: 100%;
    display: flex; align-items: center; justify-content: center; gap: 10px;
  }
  .back-brand__mark { width: 20px; height: 20px; background: var(--green); }
  .back-brand__name { font-weight: 700; font-size: 24px; color: var(--ink-soft); white-space: nowrap; }

  .services { position: absolute; left: 350px; top: 139px; color: var(--ink-soft); }
  .services__heading { font-weight: 700; font-style: italic; font-size: 27px; margin-bottom: 6px; }
  .services__list { list-style: none; }
  .services__list li { font-size: 19px; line-height: 24.8px; padding-left: 20px; position: relative; }
  .services__list li::before {
    content: ""; position: absolute; left: 3px; top: 10px;
    width: 6px; height: 6px; border-radius: 50%; background: var(--ink-soft);
  }
</style>
</head>
<body>
<div class="canvas">

  <section class="card card--front" aria-label="Business card front">
    <div class="brand-panel">
      <div class="brand-panel__mark"></div>
      <div class="brand-panel__name">NORRELL ADVISORY</div>
      <div class="brand-panel__tagline">STEADY STEPS STRONG RESULTS</div>
    </div>
    <div class="colour-stripe">
      <span class="blue"></span><span class="red"></span><span class="green"></span><span class="orange"></span>
    </div>
    <div class="contact-panel">
      <div class="person">
        <div class="person__name">Derek Holloway</div>
        <div class="person__phone">0407385510</div>
      </div>
      <div class="person">
        <div class="person__name">Megan Holloway</div>
        <div class="person__phone">0407913847</div>
      </div>
      <ul class="contact-list">
        <li>
          <svg viewBox="0 0 16 16" aria-hidden="true"><rect x="1" y="1" width="14" height="14" fill="#c9c9c9"/></svg>
          norrelladvisorywa
        </li>
        <li>
          <svg viewBox="0 0 16 16" aria-hidden="true"><rect x="1" y="3" width="14" height="10" fill="#c9c9c9"/><path d="M1 3 L8 9 L15 3" fill="none" stroke="#262626" stroke-width="1.4"/></svg>
          norrelladvisorywa@mailbox-example.com
        </li>
        <li>
          <svg viewBox="0 0 16 16" aria-hidden="true"><circle cx="8" cy="8" r="7" fill="#c9c9c9"/><path d="M1 8h14M8 1c-3 3-3 11 0 14M8 1c3 3 3 11 0 14" fill="none" stroke="#262626" stroke-width="1"/></svg>
          www.norrelladvisorywa-example.com
        </li>
      </ul>
    </div>
  </section>

  <section class="card card--back" aria-label="Business card back">
    <div class="back-brand">
      <div class="back-brand__mark"></div>
      <div class="back-brand__name">Norrell Advisory</div>
    </div>
    <div class="services">
      <h2 class="services__heading">Providing assistance with</h2>
      <ul class="services__list">
        <li>Organisation &amp; Efficiency</li>
        <li>Revenue generation &amp; Marketing</li>
        <li>Financial Management</li>
        <li>Production quality &amp; delivery</li>
        <li>Systems &amp; Process documentation</li>
        <li>Exit Strategy</li>
      </ul>
    </div>
  </section>

</div>
</body>
</html>
```